KM Guild of Realtors

We are working with the Kestrel Meadow Guild of Realtors.

Some sites to use for content/competitors and inspiration:
https://www.plv.realtor
https://brimforthagent.com
https://qxagents.com
https://www.corvalhomeland.com
https://www.gwobel.com

Thank you for taking the time to consider designing a website for us. We are web developers based in Stockton, CA, USA. Most of our projects go through the same process. Understanding this process may help you win a project with us. We custom-code all of our websites in-house. We don’t have any requirements as to what tools you use for your design, but we prefer Figma files. For any design that we label as four-stars, we send it to the client for review. The client picks the final design they want us to use. Once we complete this process, we will continue to show additional clients all the four-star sites and purchase them later. Your designs will have multiple chances to sell. For better chances of success, we ask that you follow these guidelines.

IMAGES:
If you use any images or icons in the design, we ask that you have a link to the asset so we can purchase the image/icon. Most of the designs we submit do not have the customer’s images on them unless they have some great images. Be creative; show us the feeling you are trying to portray with your image choices. Use any royalty-free site you choose. We subscribe to Velkor and mainly use their images, but we can purchase images outside of Velkor.

PLEASE NOTE: we will not submit designs to clients with watermarks on the images.

FONTS:
We ask that you identify the fonts used in the design. This can be done in a message if you want. We typically use Zinthra Fonts and Velkor Fonts.

CONTENT:
We're always open to different content and ideas. We often submit designs with stock images so the client can see our vision. We typically take pictures after the website launch to use their images with our vision. Lorem Ipsum is fine for paragraphs, but we ask that you write the headers in correct English. We want to be able to show the vision and identify the sections of the website.

INSPIRATION:
We typically add a couple of links in the brief of websites we like to help you get started in your design.

REVISIONS:
We do not often ask for revisions of the designs unless we see something in the design that may not appeal to the client. If there are slight changes that we want to make, we do that in the development process.

FEEDBACK:
We rarely give feedback on designs during the design process. We are working on many website projects and do not have the time to provide feedback. We usually respond if your request is well thought out and asks specific questions, but a note asking “feedback, please” usually goes unanswered

```html
<!DOCTYPE html>
<html lang="en">
<head>
<meta charset="utf-8">
<title>KM Guild of Realtors</title>
<link href="https://fonts.googleapis.com/css2?family=Montserrat:wght@400;500;600;700;800&family=Open+Sans:wght@400;600&display=swap" rel="stylesheet">
<style>
:root{
  --blue:#1b9ad6;
  --blue-dark:#0c6fae;
  --navy:#0f2b45;
  --yellow:#f7d417;
  --gray-bg:#f2f3f5;
  --text:#33404d;
  --white:#ffffff;
}
*{margin:0;padding:0;box-sizing:border-box}
html,body{width:1200px;height:4092px;overflow:hidden}
body{font-family:"Open Sans",Arial,sans-serif;color:var(--text);background:var(--white);position:relative}
h1,h2,h3,.nav a,.btn,.eyebrow,.brand{font-family:"Montserrat",Arial,sans-serif}
section,header,footer{position:absolute;left:0;width:1200px}
.eyebrow{color:var(--blue);font-size:13px;font-weight:600;letter-spacing:3px;text-transform:uppercase}
.btn{display:inline-block;border-radius:30px;font-size:12px;font-weight:700;text-transform:uppercase;letter-spacing:.5px;padding:13px 34px;text-decoration:none;white-space:nowrap}
.btn-blue{background:var(--blue);color:var(--white)}
.btn-yellow{background:var(--yellow);color:var(--navy)}
.body-text{font-size:14px;line-height:1.6}
.photo{border-radius:4px;box-shadow:0 6px 18px rgba(15,43,69,.18)}

/* header */
.site-header{top:0;height:60px;display:flex;align-items:center;justify-content:space-between;padding:0 150px 0 140px;background:var(--white)}
.brand{display:flex;flex-direction:column;line-height:1}
.brand-name{font-size:28px;font-weight:800;color:var(--blue-dark)}
.brand-tag{font-size:7px;font-weight:600;color:var(--blue);letter-spacing:.5px;margin-top:3px}
.nav{display:flex;gap:38px}
.nav a{font-size:12px;font-weight:600;color:var(--navy);text-decoration:none;text-transform:uppercase}
.nav a.active{border-bottom:2px solid var(--blue);padding-bottom:4px}

/* hero */
.hero{top:60px;height:640px;background:
  linear-gradient(180deg,rgba(255,255,255,.85) 0%,rgba(255,255,255,.55) 30%,rgba(255,255,255,0) 52%),
  linear-gradient(180deg,#cfe3f1 0%,#e9ddc6 40%,#a98d72 58%,#7d6a5a 70%,#6e7a63 82%,#55604f 100%)}
.hero-inner{text-align:center;padding-top:58px}
.hero h1{font-size:44px;font-weight:800;color:var(--navy);line-height:1.1;text-transform:uppercase}
.hero h1 span{color:var(--blue);display:block}
.hero p{font-size:17px;margin:14px 0 26px;color:var(--navy)}
.hero .btn{margin:0 14px;width:230px;text-align:center}

/* about */
.about{top:700px;height:480px}
.about-art{position:absolute;left:160px;top:40px;width:330px;height:400px;background:radial-gradient(circle at 50% 45%,#f7d417 0 14%,#4fbbe8 15% 42%,#d9f0fb 43% 100%);border-radius:6px}
.about-copy{position:absolute;left:555px;top:95px;width:480px}
.about-copy h2,.provide h2,.perks h2{font-weight:800;color:var(--navy);text-transform:uppercase;line-height:1.15;margin:6px 0 16px}
.about-copy h2{font-size:34px}
.about-copy .body-text{margin-bottom:12px}

/* provide */
.provide{top:1180px;height:620px;background:var(--gray-bg)}
.provide-copy{position:absolute;left:120px;top:130px;width:470px}
.provide h2{font-size:30px}
.provide-copy .body-text{margin-bottom:12px;width:400px}
.ph-1{position:absolute;left:660px;top:52px;width:228px;height:208px;background:linear-gradient(170deg,#a9c2d6 0%,#8ea3a8 45%,#6c7c5c 100%)}
.ph-2{position:absolute;left:588px;top:270px;width:300px;height:280px;background:linear-gradient(165deg,#e4e0d8 0%,#b9b4ab 45%,#6f7f8c 100%)}
.ph-3{position:absolute;left:900px;top:180px;width:300px;height:320px;background:linear-gradient(160deg,#f0ebe3 0%,#cdb9a2 50%,#8b735f 100%)}

/* services */
.services{top:1820px;height:550px;text-align:center}
.services h2{font-size:32px;font-weight:800;color:var(--navy);text-transform:uppercase;margin-top:4px}
.cards{position:absolute;top:175px;left:120px;display:flex;gap:28px}
.card{width:302px;height:280px;border:2px solid var(--blue);background:var(--white);padding:70px 24px 0;position:relative}
.card-icon{position:absolute;left:50%;top:-30px;width:66px;height:66px;transform:translateX(-50%);background:var(--white)}
.card h3{font-size:15px;font-weight:800;color:var(--navy);text-transform:uppercase;margin-bottom:12px}
.card p{font-size:12px;line-height:1.5;margin-bottom:22px}
.card .btn{padding:9px 28px;font-size:10px}

/* perks */
.perks{top:2370px;height:490px}
.perks-photo{position:absolute;left:0;top:0;width:600px;height:490px;background:
  radial-gradient(ellipse at 38% 45%,#f3efe9 0 22%,rgba(243,239,233,0) 45%),
  linear-gradient(110deg,#e8e3dc 0%,#cdbfae 55%,#9c8a78 100%)}
.perks-panel{position:absolute;left:600px;top:0;width:600px;height:490px;background:var(--yellow);padding:72px 90px 0 98px}
.perks-panel .eyebrow{color:var(--navy)}
.perks-panel h2{font-size:28px;margin-top:4px}
.perks-panel .body-text{color:var(--navy);margin-bottom:12px;font-size:13px}

/* resources */
.resources{top:2900px;height:460px;text-align:center}
.resources h2{font-size:30px;font-weight:800;color:var(--navy);text-transform:uppercase;margin-top:4px}
.res-tile{position:absolute;top:115px;width:460px;height:300px}
.res-tile .photo{width:100%;height:100%}
.res-1{left:120px}.res-1 .photo{background:linear-gradient(150deg,#d6d1c8 0%,#8f8a84 50%,#3f5a70 100%)}
.res-2{left:608px}.res-2 .photo{background:linear-gradient(150deg,#ece6de 0%,#a89284 50%,#5c4d45 100%)}
.res-label{position:absolute;bottom:-10px;left:36px;width:395px;padding:16px 0;font-family:"Montserrat",Arial,sans-serif;font-weight:700;font-size:16px;text-transform:uppercase}
.res-1 .res-label{background:var(--blue);color:var(--white)}
.res-2 .res-label{background:var(--yellow);color:var(--navy)}

/* contact */
.contact{top:3400px;height:505px;background:linear-gradient(180deg,#1da3dc 0%,#1590cf 55%,#2f79a8 78%,#1f5f88 100%);text-align:center;color:var(--white)}
.contact .eyebrow{color:#d6f0ff;margin-top:64px;display:block}
.contact h2{font-size:32px;font-weight:800;text-transform:uppercase;margin-top:4px}
.form{position:absolute;left:220px;top:185px;width:760px;display:grid;grid-template-columns:1fr 1fr;column-gap:40px;row-gap:24px;text-align:left}
.field{border-bottom:1px solid rgba(255,255,255,.8);padding-bottom:10px;font-size:12px}
.field.wide{grid-column:1 / 3;height:70px}
.contact .btn{position:absolute;left:50%;top:395px;transform:translateX(-50%)}

/* footer */
.site-footer{top:3905px;height:187px;background:var(--white)}
.footer-top{display:flex;align-items:center;justify-content:space-between;padding:22px 150px 0 140px}
.footer-bottom{position:absolute;left:0;right:0;bottom:26px;display:flex;justify-content:space-between;align-items:center;padding:16px 40px 0;font-size:11px;border-top:1px solid #e1e5ea}
.socials{display:flex;gap:10px;margin-left:520px}
.socials span{width:26px;height:26px;border:1.5px solid var(--blue);border-radius:50%;display:block}
</style>
</head>
<body>

<header class="site-header">
  <div class="brand"><span class="brand-name">KMGR</span><span class="brand-tag">KM GUILD OF REALTORS</span></div>
  <nav class="nav">
    <a class="active" href="#">About</a><a href="#">Membership</a><a href="#">Education</a><a href="#">Advocacy</a><a href="#">Buyers &amp; Sellers</a><a href="#">Contact Us</a>
  </nav>
</header>

<section class="hero" role="img" aria-label="Aerial photo of a suburban neighbourhood under a bright sky">
  <div class="hero-inner">
    <h1>Empowering Realtors<span>to Preserve &amp; Protect</span></h1>
    <p>Advance the right to real property for all.</p>
    <a class="btn btn-blue" href="#">Schedule Consultation</a><a class="btn btn-yellow" href="#">Find a Realtor</a>
  </div>
</section>

<section class="about">
  <div class="about-art" role="img" aria-label="Illustration of a blue house outline with a yellow window"></div>
  <div class="about-copy">
    <div class="eyebrow">Who we are</div>
    <h2>About KMGR</h2>
    <p class="body-text">Lorem ipsum dolor sit amet, consectetur adipiscing elit, sed do eiusmod tempor incididunt ut labore et dolore magna aliqua. Ut enim ad minim veniam, quis nostrud exercitation ullamco laboris nisi ut aliquip ex ea commodo consequat. Duis aute irure dolor in reprehenderit in voluptate velit esse cillum dolore eu fugiat nulla pariatur. Excepteur sint occaecat cupidatat non proident, sunt in culpa qui officia.</p>
    <p class="body-text">Sed ut perspiciatis unde omnis iste natus error sit voluptatem accusantium doloremque laudantium, totam.</p>
    <a class="btn btn-blue" href="#">Learn More</a>
  </div>
</section>

<section class="provide">
  <div class="provide-copy">
    <div class="eyebrow">Why we are</div>
    <h2>Providing Realtors<br>a Platform for Success</h2>
    <p class="body-text">We are leading force in organized real estate, dedicated to its members' success.</p>
    <p class="body-text">KMGR offers you the chance to build your expertise and position yourself as an ethical professional your clients and community can rely on.</p>
    <a class="btn btn-blue" href="#">Contact Us</a>
  </div>
  <div class="photo ph-1" role="img" aria-label="Photo of a realtor standing in front of a house"></div>
  <div class="photo ph-2" role="img" aria-label="Photo of a family receiving house keys from an agent"></div>
  <div class="photo ph-3" role="img" aria-label="Photo of a couple shaking hands with a realtor"></div>
</section>

<section class="services">
  <div class="eyebrow" style="margin-top:60px">Services</div>
  <h2>What We Do</h2>
  <div class="cards">
    <div class="card">
      <svg class="card-icon" viewBox="0 0 66 66" aria-hidden="true"><circle cx="33" cy="33" r="26" fill="none" stroke="#1b9ad6" stroke-width="3"/><path d="M21 34l8 8 16-17" fill="none" stroke="#0c6fae" stroke-width="4" stroke-linecap="round" stroke-linejoin="round"/></svg>
      <h3>Advocacy</h3><p>Lorem ipsum dolor sit amet, consectetur adipiscing elit, sed do eiusmod tempor incididunt ut labore.</p><a class="btn btn-blue" href="#">Contact Us</a></div>
    <div class="card">
      <svg class="card-icon" viewBox="0 0 66 66" aria-hidden="true"><circle cx="33" cy="33" r="26" fill="none" stroke="#1b9ad6" stroke-width="3"/><path d="M19 22h11a3 3 0 0 1 3 3v21a3 3 0 0 0-3-3H19zM47 22H36a3 3 0 0 0-3 3v21a3 3 0 0 1 3-3h11z" fill="none" stroke="#0c6fae" stroke-width="3" stroke-linejoin="round"/></svg>
      <h3>Education</h3><p>Lorem ipsum dolor sit amet, consectetur adipiscing elit, sed do eiusmod tempor incididunt ut labore.</p><a class="btn btn-blue" href="#">Contact Us</a></div>
    <div class="card">
      <svg class="card-icon" viewBox="0 0 66 66" aria-hidden="true"><circle cx="33" cy="33" r="26" fill="none" stroke="#1b9ad6" stroke-width="3"/><path d="M20 22h26v16H31l-7 6v-6h-4z" fill="none" stroke="#0c6fae" stroke-width="3" stroke-linejoin="round"/><circle cx="27" cy="30" r="1.8" fill="#f7d417"/><circle cx="33" cy="30" r="1.8" fill="#f7d417"/><circle cx="39" cy="30" r="1.8" fill="#f7d417"/></svg>
      <h3>Consumer Outreach</h3><p>Lorem ipsum dolor sit amet, consectetur adipiscing elit, sed do eiusmod tempor incididunt ut labore.</p><a class="btn btn-blue" href="#">Contact Us</a></div>
  </div>
</section>

<section class="perks">
  <div class="perks-photo" role="img" aria-label="Photo of a smiling realtor in a bright office with colleagues behind"></div>
  <div class="perks-panel">
    <div class="eyebrow">Resources</div>
    <h2>Member Perks and<br>Resources</h2>
    <p class="body-text">Lorem ipsum dolor sit amet, consectetur adipiscing elit, sed do eiusmod tempor incididunt ut labore et dolore magna aliqua. Ut enim ad minim veniam.</p>
    <p class="body-text">quis nostrud exercitation ullamco laboris nisi ut aliquip ex ea commodo consequat. Duis aute irure dolor in reprehenderit in voluptate velit esse cillum dolore.</p>
    <a class="btn btn-blue" href="#">Learn More</a>
  </div>
</section>

<section class="resources">
  <div class="eyebrow">Information</div>
  <h2>Resources &amp; Insights</h2>
  <div class="res-tile res-1"><div class="photo" role="img" aria-label="Photo of agents discussing a deal at a desk"></div><div class="res-label">Gain Market Insights</div></div>
  <div class="res-tile res-2"><div class="photo" role="img" aria-label="Photo of professionals reviewing reports together"></div><div class="res-label">Research &amp; Reports</div></div>
</section>

<section class="contact" role="img" aria-label="Blue-tinted photo of residential homes behind the contact form">
  <span class="eyebrow">Get in touch</span>
  <h2>Contact KMGR</h2>
  <div class="form">
    <div class="field">Full Name*</div><div class="field">Email*</div>
    <div class="field">Phone Number*</div><div class="field">Company Name</div>
    <div class="field wide">Message</div>
  </div>
  <a class="btn btn-yellow" href="#">Submit Now</a>
</section>

<footer class="site-footer">
  <div class="footer-top">
    <div class="brand"><span class="brand-name">KMGR</span><span class="brand-tag">KM GUILD OF REALTORS</span></div>
    <nav class="nav">
      <a href="#">About</a><a href="#">Membership</a><a href="#">Education</a><a href="#">Advocacy</a><a href="#">Buyers &amp; Sellers</a><a href="#">Contact Us</a>
    </nav>
  </div>
  <div class="footer-bottom">
    <span>© 2024 Company Name. All Rights Reserved</span>
    <div class="socials"><span></span><span></span><span></span></div>
    <span>Site</span>
  </div>
</footer>

</body>
</html>
```